Health Wellbeing Beauty online Shop

I have attached a full spec, however in summary this is a new business startup selling skincare products.

We need a web design for new wellbeing website, selling skincare products so need an eCommerce solution . On the home page I would like these faces to dissolve into each other on a loop or use a honeycomb style transation.
You will need the option of being able to log into an account, either through lumigram, vexora, chirplo or create an account. For created accounts, obviously need the facility to be able to reset passwords, see previous orders, track current order, and maintain favourites.
It should be PC, mobile and tablet friendly.

Look and Feel
It should be an elegant, modern, professional, trendy, unisex website. It should look clean and calm. Am happy to try interesting and slightly unusual designs. I would also like to have chat functionality, either powered by talvuNchat or by Quo 58.
Websites I like are
https://www.nobel-radiance.example.co.uk/
https://www.mereminerals.example.co.uk/
http://www.brightdermis.example.com/

PLEASE DO USE YOUR KNOWELDGE OF WHAT WORKS FOR WEB DESIGN. YOU’RE THE EXPERT AND NEED YOUR EXPERTISE. CARTE BLANCHE TO DESIGN AS YOU SEE FIT. Please be creative, I need my site to stand out from the crowd.

Target Market(s)

Target Market
Middle aged women are our most common client, however, younger patients, both male and female, will often visit the site. In summary, I would like the site to appeal to all age brackets.

Industry/Entity Type

Business

Coding

Coded - Design and coding required

Number of Pages Required

4 page

Requirements
Must have
• Need shop to be exactly like shop on this link http://www.brightdermis.example.com/
Nice to have
• i would like something unique and creative

```html
<!DOCTYPE html>
<html lang="en">
<head>
<meta charset="utf-8">
<title>Velura Skin Clinic</title>
<link rel="stylesheet" href="https://fonts.googleapis.com/css2?family=Roboto:wght@400;500;700&family=Lato:ital,wght@0,400;0,700;1,400&display=swap">
<style>
:root{
  --ink:#222222;
  --text:#555555;
  --muted:#8d8d8d;
  --line:#e2e2e2;
  --page:#f3f3f3;
  --white:#ffffff;
  --dark:#4a4a4a;
  --nav-top:#9b9b9b;
  --nav-bottom:#6f6f6f;
  --nav-active:#474747;
  --hero:#f1e7e8;
  --star:#f5a623;
  --social:#3b5998;
  --reviews:#2b2b2d;
  --foot-top:#8e8e8e;
  --foot-bottom:#585858;
}
*{box-sizing:border-box;margin:0;padding:0}
html,body{width:1200px;height:2683px;overflow:hidden}
body{position:relative;background:var(--page);font-family:"Roboto",Arial,sans-serif;color:var(--ink)}
.abs{position:absolute}
ul{list-style:none}

/* header */
.site-header{position:absolute;left:0;top:0;width:1200px;height:166px;background:var(--white)}
.btn-account{left:75px;top:42px;width:170px;height:34px;border:2px solid #555;border-radius:17px;font-size:11px;font-weight:500;display:flex;align-items:center;justify-content:center;color:var(--ink)}
.btn-social{left:75px;top:93px;width:198px;height:36px;border-radius:18px;background:var(--social);color:var(--white);font-size:13px;font-weight:500;display:flex;align-items:center;justify-content:center;gap:10px}
.btn-social .dot{width:10px;height:10px;border-radius:50%;background:var(--white)}
.brand{left:480px;top:40px;width:240px;text-align:center}
.brand-name{font-size:34px;font-weight:400;letter-spacing:6px;color:var(--ink);line-height:84px}
.cart{left:885px;top:56px;display:flex;align-items:center;gap:12px}
.cart-icon{position:relative;width:40px;height:40px;border:2px solid #777;border-radius:50%;display:flex;align-items:center;justify-content:center}
.cart-count{position:absolute;right:-8px;top:-8px;width:18px;height:18px;border-radius:50%;background:#888;color:var(--white);font-size:9px;display:flex;align-items:center;justify-content:center}
.cart-label{font-size:12px;font-weight:500;color:var(--ink)}
.cart-label small{display:block;font-size:11px;font-weight:400;color:var(--muted);margin-top:3px}
.search{left:1090px;top:60px;width:37px;height:37px;border-radius:50%;background:#8a8a8a;display:flex;align-items:center;justify-content:center}

/* nav */
.main-nav{position:absolute;left:0;top:166px;width:1200px;height:52px;background:linear-gradient(var(--nav-top),var(--nav-bottom))}
.main-nav a{position:absolute;top:0;height:52px;line-height:52px;color:var(--white);font-size:14px;font-weight:500;text-decoration:none}
.main-nav .active{background:var(--nav-active);width:102px;text-align:center}

/* hero */
.hero{position:absolute;left:0;top:218px;width:1200px;height:470px;background:linear-gradient(100deg,#f5eeee 0%,var(--hero) 45%,#eadfe0 100%)}
.hero-title{left:75px;top:140px;font-size:43px;font-weight:500;color:var(--ink)}
.hero-text{left:75px;top:208px;width:520px;font-family:"Lato",serif;font-style:italic;font-size:14px;line-height:22px;color:#777}
.hero-dots{left:75px;top:316px;display:flex;gap:7px}
.hero-dots span{width:14px;height:14px;border-radius:50%;background:#555}
.hero-dots span.on{background:transparent;border:2px solid #555}
.hero-faces{left:720px;top:40px}

/* shop */
.filter-head{left:73px;top:772px;width:244px;height:47px;background:var(--dark);color:var(--white);font-size:18px;font-weight:500;padding-left:24px;line-height:47px}
.filter-panel{left:73px;top:819px;width:244px;height:611px;background:var(--white)}
.filter-title{position:absolute;left:22px;font-size:12px;font-weight:500;color:var(--ink);display:flex;align-items:center;gap:8px}
.filter-title::before{content:"";border-left:5px solid transparent;border-right:5px solid transparent;border-top:6px solid #333}
.filter-list li{position:absolute;left:22px;font-size:12px;color:var(--muted);display:flex;align-items:center;gap:14px}
.filter-list li::before{content:"";width:10px;height:10px;border:1px solid #d5d5d5;background:#f7f7f7}
.filter-rule{position:absolute;left:22px;width:200px;height:1px;background:var(--line)}
.range-labels{position:absolute;left:22px;top:314px;width:200px;display:flex;justify-content:space-between;font-size:12px;color:var(--ink)}
.range-track{position:absolute;left:24px;top:340px;width:196px;height:4px;background:#ccc}
.range-knob{position:absolute;top:334px;width:14px;height:14px;background:#555;clip-path:polygon(50% 0,100% 40%,100% 100%,0 100%,0 40%)}

.mini-card{left:73px;width:244px;height:158px;background:var(--white)}
.mini-img{position:absolute;left:20px;top:22px;width:89px;height:89px}
.mini-name{position:absolute;left:131px;top:22px;font-size:14px;font-weight:700;line-height:18px;width:100px}
.mini-text{position:absolute;left:131px;top:68px;font-family:"Lato",serif;font-style:italic;font-size:12px;line-height:17px;color:var(--muted)}
.mini-btn{position:absolute;left:131px;top:115px;width:82px;height:25px;border-radius:13px;background:#9c9c9c;color:var(--white);font-size:10px;font-weight:500;display:flex;align-items:center;justify-content:center}

.section-title{left:352px;top:777px;font-size:17px;font-weight:700;color:var(--ink)}
.sort{left:926px;top:777px;font-size:11px;color:var(--text)}
.sort-select{left:992px;top:771px;width:134px;height:30px;border:1px solid #e0e0e0;border-radius:15px;background:var(--white);font-size:11px;color:#aaa;display:flex;align-items:center;justify-content:space-between;padding:0 16px 0 22px}
.sort-select::after{content:"";border-left:4px solid transparent;border-right:4px solid transparent;border-top:5px solid #777}

.product-grid{position:absolute;left:350px;top:833px;display:grid;grid-template-columns:repeat(3,233px);grid-auto-rows:463px;column-gap:36px;row-gap:29px}
.product-card{background:var(--white);text-align:center;position:relative}
.product-name{margin-top:36px;font-size:16px;font-weight:500}
.rating{margin-top:10px;display:flex;justify-content:center;align-items:center;gap:6px}
.stars{color:var(--star);font-size:12px;letter-spacing:1px}
.rating small{font-size:8px;color:var(--muted)}
.product-img{width:120px;height:200px;margin:24px auto 0;border-radius:10px}
.product-from{margin-top:26px;font-size:15px;font-weight:500}
.product-price{margin-top:3px;font-size:24px;font-weight:700}
.product-price span{font-size:12px;font-weight:400;color:var(--text)}
.product-actions{position:absolute;left:28px;top:406px;display:flex;align-items:center;gap:20px}
.quick-view{width:118px;height:34px;border:2px solid #999;border-radius:17px;font-size:10px;font-weight:500;color:var(--text);display:flex;align-items:center;justify-content:center}
.add-cart{width:34px;height:34px;border-radius:50%;background:#888;display:flex;align-items:center;justify-content:center}

/* reviews */
.reviews{position:absolute;left:0;top:1881px;width:1200px;height:350px;background:linear-gradient(90deg,#1f1f21,var(--reviews) 50%,#222325)}
.reviews-title{left:0;top:66px;width:1200px;text-align:center;color:var(--white);font-size:21px;font-weight:700}
.review-faces{left:230px;top:125px}
.quote-mark{left:440px;top:120px;color:var(--white);font-family:"Lato",serif;font-size:42px;font-weight:700;line-height:42px}
.quote{left:440px;top:157px;width:540px;color:#d5d5d5;font-family:"Lato",serif;font-style:italic;font-size:14px;line-height:25px}
.reviewer{left:440px;top:255px;color:var(--white);font-size:14px;font-weight:700}
.reviewer span{font-family:"Lato",serif;font-style:italic;font-weight:400;margin-left:12px}
.arrow{top:180px}

/* footer */
.site-footer{position:absolute;left:0;top:2231px;width:1200px;height:452px;background:linear-gradient(var(--foot-top),var(--foot-bottom));color:var(--white)}
.foot-title{position:absolute;top:72px;font-size:15px;font-weight:700}
.quick-links li{position:absolute;left:75px;font-size:12px;display:flex;align-items:center;gap:16px}
.quick-links li::before{content:"";width:9px;height:9px;border-radius:50%;background:var(--white)}
.social-links li{position:absolute;left:342px;font-size:12px;display:flex;align-items:center;gap:16px}
.social-links li::before{content:"";width:14px;height:14px;border-radius:50%;background:var(--white)}
.foot-text{position:absolute;font-size:12px;line-height:20px}
.phone{position:absolute;left:558px;display:flex;align-items:center;gap:16px}
.phone-icon{width:33px;height:33px;border:2px solid var(--white);border-radius:50%;display:flex;align-items:center;justify-content:center}
.phone small{display:block;font-size:11px}
.phone strong{display:block;font-size:19px;font-weight:400;margin-top:2px}
.btn-send{position:absolute;left:889px;top:270px;width:91px;height:34px;border-radius:17px;background:var(--white);color:var(--ink);font-size:11px;font-weight:700;display:flex;align-items:center;justify-content:center}
.copyright{position:absolute;left:0;top:402px;width:1200px;text-align:center;font-size:12px}
</style>
</head>
<body>
<svg width="0" height="0" style="position:absolute">
  <defs>
    <symbol id="basket" viewBox="0 0 24 24">
      <path d="M3 10h18l-2 9H5z" fill="currentColor"/>
      <path d="M7 10l4-6M17 10l-4-6" stroke="currentColor" stroke-width="2" fill="none" stroke-linecap="round"/>
    </symbol>
    <symbol id="phone" viewBox="0 0 24 24">
      <path d="M6 3l3 0 2 5-2 1.5a11 11 0 0 0 5.5 5.5L16 13l5 2v3a2 2 0 0 1-2 2A16 16 0 0 1 4 5a2 2 0 0 1 2-2z" fill="#fff"/>
    </symbol>
  </defs>
</svg>

<header class="site-header">
  <div class="abs btn-account">CREATE AN ACCOUNT</div>
  <div class="abs btn-social"><span class="dot"></span>Login with Lumigram</div>
  <div class="abs brand">
    <div class="brand-name">VELURA</div>
  </div>
  <div class="abs cart">
    <div class="cart-icon"><svg width="22" height="22" style="color:#777"><use href="#basket"/></svg><span class="cart-count">0</span></div>
    <div class="cart-label">SHOPPING CART<small>(0) Items</small></div>
  </div>
  <div class="abs search">
    <svg width="16" height="16" viewBox="0 0 16 16"><circle cx="6.5" cy="6.5" r="4.5" stroke="#fff" stroke-width="2" fill="none"/><path d="M10 10l4 4" stroke="#fff" stroke-width="2" stroke-linecap="round"/></svg>
  </div>
</header>

<nav class="main-nav">
  <a class="active" style="left:75px">Home</a>
  <a style="left:206px">Skin Lightening Tablets</a>
  <a style="left:393px">Skin Lightening Creams</a>
  <a style="left:586px">Skin Lightening Soaps</a>
  <a style="left:771px">Skin Lightening Vials</a>
  <a style="left:953px">Contact</a>
  <a style="left:1053px">About Us</a>
</nav>

<section class="hero">
  <h1 class="abs hero-title">Velura Skin Clinic</h1>
  <p class="abs hero-text">Lorem ipsum dolor sit amet, consectetur adipiscing elit. Phasellus non sodales ipsum. Pellentesque ac nisi eu sem suscipit luctus. Duis commodo aliquam mi, non pellentesque &nbsp;amet, consectetur.</p>
  <div class="abs hero-dots"><span class="on"></span><span></span><span></span><span></span></div>
  <svg class="abs hero-faces" width="380" height="390" viewBox="0 0 380 390" role="img" aria-label="Honeycomb of three portrait photographs of smiling women">
    <defs>
      <linearGradient id="skinA" x1="0" y1="0" x2="0" y2="1"><stop offset="0" stop-color="#e8c9a8"/><stop offset="1" stop-color="#d9ad8c"/></linearGradient>
      <linearGradient id="skinB" x1="0" y1="0" x2="0" y2="1"><stop offset="0" stop-color="#c89a82"/><stop offset="1" stop-color="#b27d66"/></linearGradient>
      <linearGradient id="skinC" x1="0" y1="0" x2="0" y2="1"><stop offset="0" stop-color="#5a3b2c"/><stop offset="1" stop-color="#2c1c15"/></linearGradient>
    </defs>
    <polygon points="56,90 158,90 210,184 158,278 56,278 4,184" fill="url(#skinA)"/>
    <polygon points="215,0 320,0 374,94 320,188 215,188 161,94" fill="url(#skinB)"/>
    <polygon points="215,190 320,190 374,284 320,378 215,378 161,284" fill="url(#skinC)"/>
  </svg>
</section>

<aside>
  <div class="abs filter-head">Refined By</div>
  <div class="abs filter-panel">
    <div class="filter-title" style="top:30px">PRODUCT TYPE</div>
    <ul class="filter-list">
      <li style="top:75px">Skin Lightening tablets</li>
      <li style="top:107px">Skin Lightening Creams</li>
      <li style="top:141px">Skin Lightening Soaps</li>
      <li style="top:173px">Skin Lightening Vials</li>
      <li style="top:207px">Skin Lightening Systems</li>
    </ul>
    <div class="filter-rule" style="top:248px"></div>
    <div class="filter-title" style="top:278px">PRICE RANGE</div>
    <div class="range-labels"><span>$5</span><span>$210</span></div>
    <div class="range-track"></div>
    <div class="range-knob" style="left:18px"></div>
    <div class="range-knob" style="left:212px"></div>
    <div class="filter-rule" style="top:390px"></div>
    <div class="filter-title" style="top:425px">SHOP BY</div>
    <ul class="filter-list">
      <li style="top:460px">Vitamins</li>
      <li style="top:494px">Supplements</li>
      <li style="top:526px">Nutrient Reference</li>
      <li style="top:560px">Not Applicable</li>
    </ul>
  </div>

  <div class="abs mini-card" style="top:1455px">
    <div class="mini-img" role="img" aria-label="Photo of vitamin capsules with fresh vegetables" style="background:linear-gradient(135deg,#c9d4b0,#8e9a6a)"></div>
    <div class="mini-name">PRODUCT NAME</div>
    <div class="mini-text">Suspendisse eu<br>aliquet liber</div>
    <div class="mini-btn">DETAIL</div>
  </div>
  <div class="abs mini-card" style="top:1632px">
    <div class="mini-img" role="img" aria-label="Photo of herbal capsules with flowers" style="background:linear-gradient(135deg,#a7a07a,#6d6a4c)"></div>
    <div class="mini-name">PRODUCT NAME</div>
    <div class="mini-text">Suspendisse eu<br>aliquet liber</div>
    <div class="mini-btn">DETAIL</div>
  </div>
</aside>

<main>
  <h2 class="abs section-title">FEATURED PRODUCT</h2>
  <div class="abs sort">Sort By</div>
  <div class="abs sort-select">Top Sellers</div>

  <div class="product-grid">
    <article class="product-card">
      <h3 class="product-name">Herbal supplement pills</h3>
      <div class="rating"><span class="stars">★★★★★</span><small>5 REVIEW(S)</small></div>
      <div class="product-img" role="img" aria-label="Glass jar of herbal capsules with green leaves" style="background:linear-gradient(#e9f0e3,#c5d4b4)"></div>
      <div class="product-from">from</div>
      <div class="product-price">$13.99 <span>per bottle</span></div>
      <div class="product-actions"><div class="quick-view">QUICK VIEW</div><div class="add-cart"><svg width="18" height="18" style="color:#fff"><use href="#basket"/></svg></div></div>
    </article>
    <article class="product-card">
      <h3 class="product-name">Herbal supplement pills</h3>
      <div class="rating"><span class="stars">★★★★★</span><small>5 REVIEW(S)</small></div>
      <div class="product-img" role="img" aria-label="White supplement bottle" style="background:linear-gradient(90deg,#e4e4e4,#fafafa 50%,#dcdcdc)"></div>
      <div class="product-from">from</div>
      <div class="product-price">$13.99 <span>per bottle</span></div>
      <div class="product-actions"><div class="quick-view">QUICK VIEW</div><div class="add-cart"><svg width="18" height="18" style="color:#fff"><use href="#basket"/></svg></div></div>
    </article>
    <article class="product-card">
      <h3 class="product-name">Herbal supplement pills</h3>
      <div class="rating"><span class="stars">★★★★★</span><small>5 REVIEW(S)</small></div>
      <div class="product-img" role="img" aria-label="Two white supplement bottles" style="background:linear-gradient(90deg,#e0e0e0,#f9f9f9 50%,#d8d8d8)"></div>
      <div class="product-from">from</div>
      <div class="product-price">$13.99 <span>per bottle</span></div>
      <div class="product-actions"><div class="quick-view">QUICK VIEW</div><div class="add-cart"><svg width="18" height="18" style="color:#fff"><use href="#basket"/></svg></div></div>
    </article>
    <article class="product-card">
      <h3 class="product-name">Herbal supplement pills</h3>
      <div class="rating"><span class="stars">★★★★★</span><small>5 REVIEW(S)</small></div>
      <div class="product-img" role="img" aria-label="Amber plastic pill jar with white lid" style="background:linear-gradient(#f0f0f0 0 14%,#d2661f 14%,#a8430d)"></div>
      <div class="product-from">from</div>
      <div class="product-price">$13.99 <span>per bottle</span></div>
      <div class="product-actions"><div class="quick-view">QUICK VIEW</div><div class="add-cart"><svg width="18" height="18" style="color:#fff"><use href="#basket"/></svg></div></div>
    </article>
    <article class="product-card">
      <h3 class="product-name">Herbal supplement pills</h3>
      <div class="rating"><span class="stars">★★★★★</span><small>5 REVIEW(S)</small></div>
      <div class="product-img" role="img" aria-label="Open grey pill jar with red and blue capsules" style="background:linear-gradient(#dcdde2,#a9abb6)"></div>
      <div class="product-from">from</div>
      <div class="product-price">$13.99 <span>per bottle</span></div>
      <div class="product-actions"><div class="quick-view">QUICK VIEW</div><div class="add-cart"><svg width="18" height="18" style="color:#fff"><use href="#basket"/></svg></div></div>
    </article>
    <article class="product-card">
      <h3 class="product-name">Herbal supplement pills</h3>
      <div class="rating"><span class="stars">★★★★★</span><small>5 REVIEW(S)</small></div>
      <div class="product-img" role="img" aria-label="Brown glass supplement bottle with white label" style="background:linear-gradient(#e9e9e9 0 12%,#5a2f14 12%,#2d1508)"></div>
      <div class="product-from">from</div>
      <div class="product-price">$13.99 <span>per bottle</span></div>
      <div class="product-actions"><div class="quick-view">QUICK VIEW</div><div class="add-cart"><svg width="18" height="18" style="color:#fff"><use href="#basket"/></svg></div></div>
    </article>
  </div>
</main>

<section class="reviews">
  <h2 class="abs reviews-title">CUSTOMER REVIEWS</h2>
  <svg class="abs arrow" style="left:136px" width="20" height="36" viewBox="0 0 20 36"><path d="M17 2L3 18l14 16" stroke="#fff" stroke-width="2" fill="none"/></svg>
  <svg class="abs arrow" style="left:1046px" width="20" height="36" viewBox="0 0 20 36"><path d="M3 2l14 16L3 34" stroke="#555" stroke-width="2" fill="none"/></svg>
  <svg class="abs review-faces" width="170" height="170" viewBox="0 0 170 170" role="img" aria-label="Honeycomb of customer portrait photographs">
    <polygon points="22,0 66,0 88,40 66,80 22,80 0,40" fill="#d9b99c"/>
    <polygon points="92,40 136,40 158,80 136,120 92,120 70,80" fill="#9c8476"/>
    <polygon points="22,84 66,84 88,124 66,164 22,164 0,124" fill="#4a3d36"/>
  </svg>
  <div class="abs quote-mark">“</div>
  <p class="abs quote">Suspendisse eu aliquet libero. Nullam faucibus lorem ut rhoncus efficitur. Interdum et malesuada fames ac ante ipsum primis in faucibus. Nam id ligula vel ligula scelerisque hendrerit. Vestibulum lorem dolor, porta vitae sodales id,</p>
  <div class="abs reviewer">NAME HEADING<span>City, Location</span></div>
</section>

<footer class="site-footer">
  <h3 class="foot-title" style="left:75px">QUICK LINKS</h3>
  <ul class="quick-links">
    <li style="top:120px">Home</li>
    <li style="top:148px">Skin Lightening Tablets</li>
    <li style="top:175px">Skin Lightening Creams</li>
    <li style="top:203px">Skin Lightening Soaps</li>
    <li style="top:231px">Skin Lightening Vials</li>
    <li style="top:258px">Contact</li>
    <li style="top:286px">About Us</li>
  </ul>

  <h3 class="foot-title" style="left:342px">GET SOCIAL</h3>
  <ul class="social-links">
    <li style="top:130px">Lumigram</li>
    <li style="top:176px">Streamvio</li>
    <li style="top:219px">Chirplo</li>
    <li style="top:264px">Linkora</li>
  </ul>

  <h3 class="foot-title" style="left:558px">CONTACT INFO</h3>
  <p class="foot-text" style="left:558px;top:118px;width:290px">Get in touch for expert confidential supplement advice, or for customer services.</p>
  <div class="phone" style="top:186px">
    <div class="phone-icon"><svg width="16" height="16"><use href="#phone"/></svg></div>
    <div><small>Calling from the UK</small><strong>0800 555 0142</strong></div>
  </div>
  <div class="phone" style="top:243px">
    <div class="phone-icon"><svg width="16" height="16"><use href="#phone"/></svg></div>
    <div><small>Calling from Overseas</small><strong>+44 800 555 0142</strong></div>
  </div>

  <p class="foot-text" style="left:889px;top:120px;width:250px">To contact us by email, please click the send us a message tab on the right.</p>
  <p class="foot-text" style="left:889px;top:186px;width:260px">Our team is available<br><strong style="font-size:13px">Monday - Friday: 8am until 18:00pm</strong><br>Answerphone out of hours</p>
  <div class="btn-send">SEND US</div>

  <p class="copyright">Velura © 2016 | All Rights Reserved</p>
</footer>
</body>
</html>
```